Modern Business Card

Modern professional business card with more than just logo and demographic info. Something memorable.

We are a trendy/modern chiropractic group with an emphasis on neurology, hence the minimalist-type brain logo. We want to convey that modern and technical aspect with professionalism and the elite nature of our practice environment.

```html
<!DOCTYPE html>
<html lang="en">
<head>
<meta charset="utf-8">
<title>Summit Chiropractic – Business Card</title>
<link href="https://fonts.googleapis.com/css2?family=Open+Sans:wght@400;600&family=Arimo:wght@700&display=swap" rel="stylesheet">
<style>
  :root {
    --backdrop: #3a3633;
    --card-white: #ffffff;
    --brand-blue: #4680c2;
    --front-tint: #eaf0f8;
    --back-tint: rgba(255, 255, 255, 0.12);
    --ink: #1d1d1d;
    --muted: #5a5a5a;
  }
  * { box-sizing: border-box; margin: 0; padding: 0; }
  html, body {
    width: 1200px; height: 716px; overflow: hidden;
    background: var(--backdrop);
    font-family: "Open Sans", Arial, sans-serif;
  }
  .canvas {
    position: relative; width: 1200px; height: 716px;
    display: flex; align-items: center; justify-content: center; gap: 40px;
  }
  .card {
    position: relative; width: 520px; height: 300px; overflow: hidden;
    box-shadow: 0 10px 30px rgba(0,0,0,.45);
  }
  .card--front { background: var(--card-white); }
  .card--back { background: var(--brand-blue); }

  .decor {
    position: absolute; border-radius: 50%;
  }
  .card--front .decor {
    width: 320px; height: 320px; right: -70px; bottom: -150px;
    background: var(--front-tint);
  }
  .card--back .decor {
    width: 320px; height: 320px; left: -110px; top: -120px;
    background: var(--back-tint);
  }

  .wordmark { position: absolute; font-family: "Open Sans", Arial, sans-serif; font-weight: 600; line-height: 1; }
  .wordmark__name { display: block; letter-spacing: .06em; }
  .wordmark__sub { display: block; letter-spacing: .12em; }

  .card--front .wordmark { left: 56px; top: 34px; color: var(--ink); }
  .card--front .wordmark__name { font-size: 24px; }
  .card--front .wordmark__sub { font-size: 11.5px; margin-top: 3px; }

  .holder {
    position: absolute; left: 40px; top: 100px;
    border-left: 5px solid var(--brand-blue); padding-left: 12px;
  }
  .holder__name {
    font-family: "Arimo", Arial, sans-serif; font-weight: 700;
    font-size: 16px; color: var(--brand-blue); letter-spacing: .02em;
  }
  .holder__title { font-size: 11px; color: var(--muted); margin-top: 2px; }

  .address {
    position: absolute; left: 57px; top: 156px;
    font-size: 11px; line-height: 1.45; color: var(--muted); font-style: normal;
  }
  .contacts {
    position: absolute; left: 40px; top: 196px; list-style: none;
    font-size: 11px; line-height: 1.65; color: var(--muted);
  }
  .contacts li { display: flex; align-items: center; gap: 7px; }
  .contacts svg { width: 10px; height: 10px; fill: var(--brand-blue); flex: none; }
  .contacts .accent { color: var(--brand-blue); }

  .card--back .wordmark { right: 46px; bottom: 46px; color: var(--card-white); }
  .card--back .wordmark__name { font-size: 40px; }
  .card--back .wordmark__sub { font-size: 19px; margin-top: 4px; }
</style>
</head>
<body>
<main class="canvas">
  <section class="card card--front" aria-label="Card front">
    <div class="decor" role="img" aria-label="Large faint brand pattern"></div>
    <div class="wordmark">
      <span class="wordmark__name">SUMMIT</span>
      <span class="wordmark__sub">CHIROPRACTIC</span>
    </div>
    <div class="holder">
      <p class="holder__name">DANIEL MOREAU</p>
      <p class="holder__title">Senior Partner</p>
    </div>
    <address class="address">
      12 Kestrel Road Westdene,<br>Cape Town, 7441
    </address>
    <ul class="contacts">
      <li>
        <svg viewBox="0 0 10 10" aria-hidden="true"><path d="M2 0.5 L3.8 2.6 L2.9 3.8 Q4 6 6.2 7.1 L7.4 6.2 L9.5 8 L8.3 9.5 Q3.5 9 0.5 1.7 Z"/></svg>
        +120 5550 1847
      </li>
      <li>
        <svg viewBox="0 0 10 10" aria-hidden="true"><path d="M2.5 0 H7.5 V10 H2.5 Z M3.4 1 V8 H6.6 V1 Z"/></svg>
        +965 5550 2716
      </li>
      <li>
        <svg viewBox="0 0 10 10" aria-hidden="true"><path d="M0 2 H10 V8.5 H0 Z"/><path d="M0.5 2.4 L5 5.6 L9.5 2.4" stroke="#fff" stroke-width="0.9" fill="none"/></svg>
        info@summitchiropractic.com
      </li>
      <li>
        <svg viewBox="0 0 10 10" aria-hidden="true"><circle cx="5" cy="5" r="4.8"/><path d="M0.5 5 H9.5 M5 0.3 V9.7" stroke="#fff" stroke-width="0.7"/></svg>
        <span>www.<span class="accent">summitchiropractic</span>.com</span>
      </li>
    </ul>
  </section>

  <section class="card card--back" aria-label="Card back">
    <div class="decor" role="img" aria-label="Large faint brand pattern"></div>
    <div class="wordmark">
      <span class="wordmark__name">SUMMIT</span>
      <span class="wordmark__sub">CHIROPRACTIC</span>
    </div>
  </section>
</main>
</body>
</html>
```